Stylish Business Cards Wanted

- DOUBLE SIDED Design Required -

High end, edgy cards for a corporate and personal stylist. Must include logo,
Name: Belinda Harwick
Title: Director and Stylist
telephone : +61 8 7142 5809
email: belinda@theloombriefing.example
website: theloombriefing.example
Tag: Corporate Workwear & Uniform Specialist | Personal Stylist
Would like nice icons for telephone, email, website

Target Market(s)

Businesses wanting stylish uniforms, people wanting stylish wardrobes

Industry/Entity Type

Corporate Workwear Stylist

Contact Information for Business Card

I would like black, white and gold foiling incorporated in the design - possibly a touch of the other colours on my branding guide attached Name: Belinda Harwick Title: Director and Stylist telephone : +61 8 7142 5809 email: belinda@theloombriefing.example website: theloombriefing.example Tag: Corporate Workwear & Uniform Specialist | Personal Stylist Would like nice icons for telephone, email, website

Font styles to use
Other font styles liked:
• Raleway

Colors

Designer to choose colors to be used in the design.

Requirements
Must have
• Gold foil accents

```html
<!DOCTYPE html>
<html lang="en">
<head>
<meta charset="utf-8">
<title>The Loom Briefing – Business Card</title>
<link rel="stylesheet" href="https://fonts.googleapis.com/css2?family=Dancing+Script:wght@500;600&family=Roboto:wght@400;500&display=swap">
<style>
  :root {
    --page: #d8d3cc;
    --card: #f3f1ee;
    --navy: #1f2640;
    --gold: #c9a24a;
    --gold-light: #e2c46f;
    --ink: #1d1d22;
    --accent-pink: #c2305e;
  }
  * { margin: 0; padding: 0; box-sizing: border-box; }
  html, body { width: 1200px; height: 1054px; overflow: hidden; }
  body { background: var(--page); position: relative; font-family: "Roboto", sans-serif; }

  .card {
    position: absolute; left: 100px; top: 224px;
    width: 1000px; height: 606px;
    background: var(--card);
    border-radius: 26px;
    overflow: hidden;
    box-shadow: 0 10px 30px rgba(0,0,0,0.12);
  }

  .brand-name {
    position: absolute; left: 51px; top: 118px;
    font-family: "Roboto", sans-serif; font-weight: 500;
    font-size: 50px; line-height: 1.1; color: var(--navy);
  }

  .tagline {
    position: absolute; right: 34px; top: 92px;
    text-align: right;
    font-family: "Dancing Script", cursive; font-weight: 600;
    font-size: 31px; line-height: 41px; color: var(--ink);
  }
  .tagline .marker { color: var(--accent-pink); font-family: "Roboto", sans-serif; font-size: 20px; margin-left: 10px; display: inline-block; width: 14px; }
  .tagline .marker.blank { visibility: hidden; }

  .contact-list { position: absolute; left: 521px; top: 362px; list-style: none; }
  .contact-list li { display: flex; align-items: center; height: 41.5px; font-size: 25px; color: var(--ink); }
  .contact-list svg { width: 22px; height: 22px; margin-right: 17px; flex: none; }

  .person { position: absolute; left: 51px; top: 430px; }
  .person-name { font-family: "Dancing Script", cursive; font-weight: 600; font-size: 46px; color: var(--gold); line-height: 1.1; }
  .person-title { font-size: 25px; color: var(--ink); margin-top: 6px; }

  .bands { position: absolute; left: 0; top: 0; }

  .social-handle {
    position: absolute; left: 711px; top: 548px;
    display: flex; align-items: center; gap: 16px;
    font-size: 25px; color: var(--ink);
  }
  .social-handle .chip { width: 24px; height: 24px; border-radius: 5px; background: var(--navy); }
</style>
</head>
<body>
  <div class="card">
    <svg class="bands" width="1000" height="606" viewBox="0 0 1000 606" aria-hidden="true">
      <defs>
        <linearGradient id="goldFoil" x1="0" y1="0" x2="1" y2="1">
          <stop offset="0" stop-color="#b88d35"/>
          <stop offset="0.45" stop-color="#e2c46f"/>
          <stop offset="1" stop-color="#c49a3f"/>
        </linearGradient>
      </defs>
      <rect class="navy-band" x="0" y="584" width="430" height="22" fill="var(--navy)"/>
      <path class="gold-band" d="M445 531 H1000 V606 H406 Z" fill="url(#goldFoil)"/>
    </svg>

    <div class="brand-name">The Loom<br>Briefing</div>

    <div class="tagline">
      <div>Corporate Workwear<span class="marker">«</span></div>
      <div>&amp; Uniform Specialist<span class="marker blank">«</span></div>
      <div>Personal Stylist<span class="marker">«</span></div>
    </div>

    <ul class="contact-list">
      <li>
        <svg viewBox="0 0 24 24" fill="none" stroke="var(--gold)" stroke-width="1.8"><circle cx="12" cy="12" r="10.5"/><path d="M8.5 7.5c-.6.6-.8 1.6 0 3 1 1.8 2.4 3.3 4.2 4.3 1.3.8 2.3.6 2.9 0l.7-.8-1.9-1.6-1 .7c-1.1-.5-2.1-1.5-2.7-2.6l.7-1L9.8 7.5z" fill="var(--gold)" stroke="none"/></svg>
        +61 8 7142 5809
      </li>
      <li>
        <svg viewBox="0 0 24 24" fill="none" stroke="var(--gold)" stroke-width="1.8"><rect x="2.5" y="5" width="19" height="14" rx="1"/><path d="M3 6l9 7 9-7"/></svg>
        belinda@theloombriefing.example
      </li>
      <li>
        <svg viewBox="0 0 24 24" fill="none" stroke="var(--gold)" stroke-width="1.6"><circle cx="12" cy="12" r="10"/><ellipse cx="12" cy="12" rx="4.5" ry="10"/><path d="M2 12h20M4 7h16M4 17h16"/></svg>
        www.theloombriefing.example
      </li>
    </ul>

    <div class="person">
      <div class="person-name">Belinda Harwick</div>
      <div class="person-title">Director and Stylist</div>
    </div>

    <div class="social-handle"><span class="chip"></span>/theloombriefing101</div>
  </div>
</body>
</html>
```